Brightwell Aero Services Logo

I need a website and logo for the parent company Brightwell Aero Services, which encompasses general aviation aircraft repair, small aircrat rental and flight school. The company is based in Lawrenceville, Georgia at the Tolleson county airport. A saying that can be incorporated somehere could be, "Quality flying is safe flying", "Safety in mind is no accident" ,. I need a website and logo.

The company started as a repair shop performing repairs and inspections on Harlan, Vantor, Delkin and Ralstead general aviation aircraft, all models of single engine piston, multi engine piston, and single engine turboprop with an emphasis on Harlan Solvane and AeroTurn turbo prop aircraft. We have se=ince entered the aircraft rental and flight instruction market using the Delkin 240 ang Harlan Ranger aircraft.

Number of Pages; I don't know. Maybe 5 ? A home page for Brightwell Aero Services, page for maintenance and repairs and a couple for the rental and school. The maintenance shop is busy, always has been. I need to get the rental and school advertised and busy.

I have a logo for the maintenance shop shirts, not for the school. I do not have the file. I paid a business locally to do that and print on the shirts. They have the file.

Target Market(s)

In our flight school rental fleet department, we are looking for persons wishing to obtain their private pilot license and continuing on into their commercial and instrument ratings. In the aircraft maintenance department, we are looking for new customers who want a better and more quality relationship with their aircraft maintenance provider who will give more detail and quality in the repairs with an emphasis on safety and fewer problems between scheduled maintenance cycles on their aircraft. Brightwell's owner, Dale Hutchins, has been performing aircraft maintenance in the Atlanta area for 27 years. He has built a steady customer base through those years.

```html
<!DOCTYPE html>
<html lang="en">
<head>
<meta charset="utf-8">
<title>Brightwell Aero Services</title>
<link href="https://fonts.googleapis.com/css2?family=Montserrat:wght@400;500;600;700&display=swap" rel="stylesheet">
<style>
:root{--orange:#f4441f;--dark:#2b2b2b;--ink:#1d1d1d;--muted:#6d6d6d;--blush:#fff7f5;--line:#e4e4e4;--foot:#1a1a1a;--bar:#3a1008;--tint:#fbd3c8}
*{margin:0;padding:0;box-sizing:border-box}
html,body{width:1200px;height:3029px;overflow:hidden}
body{position:relative;font-family:'Montserrat',sans-serif;color:var(--ink);background:#fff}
.abs{position:absolute}
.logo{font-weight:700;color:var(--ink);line-height:1.15}
.tagline{display:block;font-weight:400;color:var(--orange);letter-spacing:4px}
.contact{display:flex;align-items:center;gap:12px;top:18px}
.ring{width:38px;height:38px;border-radius:50%;border:1.5px solid #f6b5a6;display:flex;align-items:center;justify-content:center}
.contact small{display:block;font-size:10px;color:var(--muted)}
.contact b{font-size:13px;font-weight:600}
.contact span{font-size:14px}
.social{display:flex;gap:10px}
.social i{width:34px;height:34px;border-radius:50%;border:1.5px solid #f6b5a6;display:block}
.nav{display:flex;gap:40px;font-size:13px;color:#333}
.nav .on{color:var(--orange);font-weight:600;position:relative}
.hero-photo{left:0;top:120px;width:1200px;height:480px;background:linear-gradient(90deg,#4a4340,#6b5d55 55%,#3a3430)}
.panel{left:150px;top:206px;width:581px;height:346px;background:rgba(30,30,30,.88);border-radius:50px 0 0 0;color:#fff;padding:56px 40px 0 68px}
.panel h1{font-size:19px;font-weight:500;line-height:1.4;width:470px}
.panel hr{border:0;border-top:1px solid #555;margin:10px 0 14px -32px;width:505px}
.panel p{font-size:13px;line-height:1.65;color:#ddd;width:430px}
.btn{display:inline-block;background:var(--orange);color:#fff;border-radius:22px;font-size:14px;padding:10px 20px}
.brandbox{left:637px;top:519px;width:310px;height:162px;background:var(--orange);border-radius:0 0 0 60px;color:#fff;text-align:center;padding-top:48px;font-weight:700;font-size:24px}
.brandbox .tagline{color:#fff;font-size:15px;letter-spacing:5px;margin-top:4px}
.arrows{left:974px;top:536px;width:161px;height:64px;background:#111;border-radius:10px;display:flex}
.arrows div{flex:1;display:flex;align-items:center;justify-content:center}
.about-photo{left:161px;top:735px;width:407px;height:366px;background:linear-gradient(135deg,#223040,#5b5650 60%,#2c2a28);border-radius:60px 0 0 0}
.about-back{left:172px;top:748px;width:407px;height:363px;background:var(--orange)}
.h2{font-size:27px;font-weight:700}
.about-txt{left:626px;top:745px;width:420px}
.about-txt .lead{font-size:14.5px;font-weight:600;line-height:1.7;margin:18px 0 12px}
.about-txt p{font-size:12.5px;line-height:1.85;color:var(--muted)}
.darkbtn{display:inline-block;background:#111;color:#fff;border-radius:22px;font-size:14px;padding:10px 20px}
.services-bg{left:0;top:1164px;width:1200px;height:682px;background:linear-gradient(#fff6f3,#fff)}
.cards{left:161px;top:1288px;width:877px;display:grid;grid-template-columns:repeat(4,1fr)}
.card{height:268px;padding:48px 20px 0 21px;position:relative;overflow:hidden}
.card h3{font-size:16px;font-weight:600;margin-bottom:8px}
.card p{font-size:12px;line-height:1.6;color:var(--muted)}
.card a{display:block;font-size:13px;color:var(--orange);text-decoration:underline;font-weight:600;margin:10px 0 22px}
.card .ico{width:58px;height:50px;border-radius:6px;background:linear-gradient(135deg,var(--tint),#f7a48f)}
.card.light{background:#fff;color:var(--ink)}
.card.dark{background:var(--dark);color:#fff}
.card.dark p{color:#ddd}
.card.dark .ico{background:linear-gradient(135deg,#6a5a55,#b5513a)}
.tri-tl{position:absolute;left:0;top:0;border-top:30px solid var(--orange);border-right:30px solid transparent}
.tri-br{position:absolute;right:0;bottom:0;border-bottom:30px solid var(--orange);border-left:30px solid transparent}
.shot{height:169px}
.stats{left:161px;top:1860px;width:877px;height:214px;border:1px dashed #c9c9c9;border-radius:30px 0 40px 0;display:grid;grid-template-columns:repeat(3,1fr);text-align:center}
.stats div{padding-top:28px;border-right:1px dashed #c9c9c9}
.stats div:last-child{border:0}
.stats strong{display:block;font-size:34px;color:var(--orange);font-weight:600}
.stats h4{font-size:16px;font-weight:600;margin:12px 0 8px}
.stats p{font-size:12.5px;line-height:1.7;color:var(--muted);padding:0 38px}
.fb{top:2185px;width:276px;height:195px;background:#fff;box-shadow:0 2px 14px rgba(0,0,0,.06);padding:18px 18px}
.fb .who{display:flex;gap:12px;align-items:center;margin-bottom:20px}
.fb .av{width:48px;height:48px;border-radius:50%;background:#c9d4dc}
.fb b{font-size:13.5px;font-weight:600;display:block}
.fb small{font-size:11px;color:var(--muted)}
.fb p{font-size:12.5px;line-height:1.8;color:var(--muted)}
.stars{color:#999;font-size:13px;letter-spacing:3px;margin-top:10px}
.sq{top:2408px;width:56px;height:46px;display:flex;align-items:center;justify-content:center}
.footer{left:0;top:2608px;width:1200px;height:365px;background:linear-gradient(#1b1b1b,#232323)}
.news{left:156px;top:2526px;width:888px;height:178px;border:5px solid #fff;background:#2a2a2a;color:#fff}
.news h2{position:absolute;left:40px;top:38px;font-size:32px;font-weight:700}
.news p{position:absolute;left:40px;top:94px;font-size:13.5px;line-height:1.9;color:#ddd}
.news .field{position:absolute;left:466px;top:21px;width:377px;height:56px;background:#fff;border-radius:4px;color:#777;font-size:14px;display:flex;align-items:center;justify-content:center}
.news .sub-btn{position:absolute;left:466px;top:92px;width:377px;height:56px;background:var(--orange);border-radius:4px;font-size:15px;font-weight:600;display:flex;align-items:center;justify-content:center}
.flogo{left:0;top:2750px;width:1200px;text-align:center;color:#fff;font-weight:700;font-size:28px;line-height:1.1}
.flogo .tagline{font-size:16px;letter-spacing:6px;margin-top:4px}
.fsocial i{border-color:var(--orange)}
.fnav{left:0;top:2918px;width:1200px;justify-content:center;color:#ddd}
.bottom{left:0;top:2973px;width:1200px;height:56px;background:var(--bar);color:#eee;font-size:13.5px;text-align:center;line-height:56px}
</style>
</head>
<body>

<header>
  <div class="abs logo" style="left:161px;top:15px;font-size:21px">Brightwell Aero<span class="tagline" style="font-size:13px;margin-top:3px">REPAIR SERVICES</span></div>
  <div class="abs contact" style="left:458px">
    <div class="ring"><svg width="16" height="16" viewBox="0 0 24 24"><path fill="#f4441f" d="M6.6 10.8a15 15 0 0 0 6.6 6.6l2.2-2.2c.3-.3.7-.4 1-.2 1.1.4 2.3.6 3.6.6.6 0 1 .4 1 1V20c0 .6-.4 1-1 1A17 17 0 0 1 3 4c0-.6.4-1 1-1h3.5c.6 0 1 .4 1 1 0 1.3.2 2.5.6 3.6.1.3 0 .7-.2 1z"/></svg></div>
    <div><small>Call No :</small><b>123, 456, 7890</b></div>
  </div>
  <div class="abs contact" style="left:630px">
    <div class="ring"><svg width="16" height="14" viewBox="0 0 24 20"><rect x="1" y="2" width="22" height="16" rx="2" fill="#f4441f"/><path d="M2 4l10 7 10-7" stroke="#fff" stroke-width="2" fill="none"/></svg></div>
    <div><small>Email ID :</small><span>brightwellaero@email.com</span></div>
  </div>
  <div class="abs social" style="left:912px;top:20px" aria-label="Social links"><i></i><i></i><i></i></div>
</header>

<div class="abs" style="left:0;top:75px;width:330px;height:30px;background:var(--orange)"></div>
<svg class="abs" style="left:320px;top:75px" width="40" height="45"><polygon points="0,0 10,0 40,45 30,45" fill="#f4441f"/></svg>
<nav class="abs nav" style="left:368px;top:90px">
  <span class="on">Home<span class="abs" style="left:-8px;top:24px;width:66px;height:3px;background:var(--orange)"></span></span>
  <span>Aviation Services</span><span>Maintenance And Repairs</span><span>Rental</span><span>School</span><span>Conatct Us</span>
</nav>

<section>
  <div class="abs hero-photo" role="img" aria-label="Two aircraft mechanics in safety glasses reviewing a laptop beside an engine"></div>
  <div class="abs panel">
    <h1>Parent Company Brightwell Aero Services, Which Encompasses General Aviation A ircraft Repair, Small Aircraft Rental And Flight School.</h1>
    <hr>
    <p>Lorem ipsum dolor sit amet, consectetuer adipiscing elit, sed diam nonummy nibh euismod tincidunt ut laoreet dolore magna aliquam erat volutpat. Ut wisi enim ad..</p>
    <div style="display:flex;align-items:center;gap:14px;margin-top:22px">
      <span class="btn">Read More</span>
      <div class="ring" style="border-color:#f4441f"><svg width="16" height="16" viewBox="0 0 24 24"><path fill="#f4441f" d="M6.6 10.8a15 15 0 0 0 6.6 6.6l2.2-2.2c.3-.3.7-.4 1-.2 1.1.4 2.3.6 3.6.6.6 0 1 .4 1 1V20c0 .6-.4 1-1 1A17 17 0 0 1 3 4c0-.6.4-1 1-1h3.5c.6 0 1 .4 1 1 0 1.3.2 2.5.6 3.6.1.3 0 .7-.2 1z"/></svg></div>
      <b style="font-size:19px;font-weight:600">123, 456, 7890</b>
    </div>
  </div>
  <div class="abs brandbox">Brightwell Aero<span class="tagline">REPAIR SERVICES</span></div>
  <div class="abs arrows">
    <div style="border-right:1px solid #333"><svg width="40" height="20"><path d="M39 10H3M11 2L3 10l8 8" stroke="#fff" stroke-width="2.5" fill="none"/></svg></div>
    <div><svg width="40" height="20"><path d="M1 10h36M29 2l8 8-8 8" stroke="#f4441f" stroke-width="2.5" fill="none"/></svg></div>
  </div>
</section>

<section>
  <div class="abs about-back"></div>
  <div class="abs about-photo" role="img" aria-label="Smiling aircraft technician with ear defenders working on an engine"></div>
  <div class="abs about-txt">
    <div class="h2" style="display:flex;align-items:center;gap:4px"><span style="width:22px;height:2px;background:var(--orange)"></span>About Us</div>
    <div class="lead">Parent Company Brightwell Aero Services, Which Encompasses General Aviation A ircraft Repair, Small Aircraft Rental And Flight School.</div>
    <p>Lorem ipsum dolor sit amet, consectetuer adipiscing elit, sed diam nonummy nibh euismod tincidunt ut laoreet dolore magna aliquam erat volutpat. Ut wisi enim ad minim veniam, quis nostrud exerci tation ullamcorper suscipit lobortis nisl ut aliquip ex ea commodo consequat. Duis autem vel eum iriure dolor in hendrerit in vulputate velit esse molestie consequat, vel illum dolore eu feugiat nulla facilisis at vero eros et accumsan et iusto...</p>
    <span class="darkbtn" style="margin-top:20px">Contact Us</span>
  </div>
</section>

<section>
  <div class="abs services-bg"></div>
  <div class="abs h2" style="left:0;top:1230px;width:1200px;text-align:center">Aviation Services</div>
  <div class="abs cards">
    <div class="card light"><span class="tri-tl"></span><span class="tri-br"></span><h3>Aircraft Repair</h3><p>Orem ipsum dolor sit amet, consectetuer adipiscing elit, sed diam nonummy nibh...</p><a>Read More</a><div class="ico" role="img" aria-label="Engine repair icon"></div></div>
    <div class="card dark"><h3>Small Aircraft Rental</h3><p>korem ipsum dolor sit amet, consectetuer adipiscing elit, sed diam nonummy nibh...</p><a>Read More</a><div class="ico" role="img" aria-label="Airplane icon"></div></div>
    <div class="card light"><span class="tri-tl"></span><span class="tri-br"></span><h3>Flight School</h3><p>Corem ipsum dolor sit amet, consectetuer adipiscing elit, sed diam nonummy nibh...</p><a>Read More</a><div class="ico" role="img" aria-label="Classroom icon"></div></div>
    <div class="card dark"><h3>Maintenance and Aircraft</h3><p>Borem ipsum dolor sit amet, consectetuer adipiscing elit, sed diam nonummy nibh...</p><a>Read More</a><div class="ico" role="img" aria-label="Gear and wrench icon"></div></div>
    <div class="shot" role="img" aria-label="Jet engine on a stand in a hangar" style="background:linear-gradient(135deg,#2a3540,#6a6e6a)"></div>
    <div class="shot" role="img" aria-label="Small propeller aircraft on grass" style="background:linear-gradient(#b8c6cf,#7d9660)"></div>
    <div class="shot" role="img" aria-label="Pilot hands at a cockpit instrument panel" style="background:linear-gradient(135deg,#3a3a38,#8a7a66)"></div>
    <div class="shot" role="img" aria-label="Passenger jet parked on an apron" style="background:linear-gradient(#c6c8cc,#8f9398)"></div>
  </div>
  <div class="abs" style="left:0;top:1764px;width:1200px;text-align:center"><span class="darkbtn">View All Services</span></div>
</section>

<section>
  <div class="abs stats">
    <div><strong>1,000</strong><h4>Pilots Assisted &amp; Assessed</h4><p>Lorem ipsum dolor sit amet, consectetuer adipiscing elit, sed diam nonummy nibh euismod tincidunt ut laor..</p></div>
    <div><strong>37</strong><h4>Airlines &amp; Flight Schools</h4><p>Lorem ipsum dolor sit amet, consectetuer adipiscing elit, sed diam nonummy nibh euismod tincidunt ut laor..</p></div>
    <div><strong>99%</strong><h4>Success Rate</h4><p>Lorem ipsum dolor sit amet, consectetuer adipiscing elit, sed diam nonummy nibh euismod tincidunt ut laor..</p></div>
  </div>
</section>

<section>
  <div class="abs h2" style="left:161px;top:2126px;display:flex;align-items:center;gap:4px"><span style="width:22px;height:2px;background:var(--orange)"></span>Recent Feedback</div>
  <div class="abs fb" style="left:161px"><div class="who"><div class="av" role="img" aria-label="Customer portrait"></div><div><b>Owen, Marsh &amp; Teller</b><small>Ipsum dolor Sit</small></div></div><p>Lorem ipsum dolor sit amet, ectetuer adipiscing elit, sed diam nonummy nibh euismod tincidunt ut...</p><div class="stars">★★★★<span style="color:#ddd">★</span></div></div>
  <div class="abs fb" style="left:461px"><div class="who"><div class="av" role="img" aria-label="Customer portrait"></div><div><b>Nora, Abc</b><small>Ipsum dolor Sit</small></div></div><p>Lorem ipsum dolor sit amet, ectetuer adipiscing elit, sed diam nonummy nibh euismod tincidunt ut...</p><div class="stars">★★★★<span style="color:#ddd">★</span></div></div>
  <div class="abs fb" style="left:761px"><div class="who"><div class="av" role="img" aria-label="Customer portrait"></div><div><b>Elias from Dunmore</b><small>Ipsum dolor Sit</small></div></div><p>Lorem ipsum dolor sit amet, ectetuer adipiscing elit, sed diam nonummy nibh euismod tincidunt ut...</p><div class="stars">★★★★<span style="color:#ddd">★</span></div></div>
  <div class="abs fb" style="left:1061px"><div class="who"><div class="av" role="img" aria-label="Customer portrait"></div><div><b>Grant from Ashby</b><small>Ipsum dolor Sit</small></div></div><p>Lorem ipsum dolor sit amet, ectetuer adipiscing elit, sed diam nonummy nibh euismod tincidunt ut...</p><div class="stars">★★★★<span style="color:#ddd">★</span></div></div>
  <div class="abs sq" style="left:161px;background:#ddd"><svg width="30" height="16"><path d="M29 8H3M9 2L3 8l6 6" stroke="#333" stroke-width="2" fill="none"/></svg></div>
  <div class="abs sq" style="left:225px;background:var(--orange)"><svg width="30" height="16"><path d="M1 8h26M21 2l6 6-6 6" stroke="#fff" stroke-width="2" fill="none"/></svg></div>
</section>

<footer>
  <div class="abs footer" role="img" aria-label="Dim hangar with parked aircraft"></div>
  <div class="abs news">
    <h2>Newsletter Sign Up</h2>
    <p>Lorem ipsum dolor sit amet, ectetuer adipiscing elit,<br>sed diam nonummy nibh euismod tincidunt ut...</p>
    <div class="field">Year Gmail Id Add*</div>
    <div class="sub-btn">Subscribe</div>
  </div>
  <div class="abs flogo">Brightwell Aero<span class="tagline">REPAIR SERVICES</span></div>
  <div class="abs social fsocial" style="left:532px;top:2828px" aria-label="Social links"><i></i><i></i><i></i></div>
  <div class="abs" style="left:161px;top:2893px;width:877px;height:1px;background:#444"></div>
  <nav class="abs nav fnav"><span class="on">Home</span><span>Aviation Services</span><span>Maintenance And Repairs</span><span>Rental</span><span>School</span><span>Conatct Us</span></nav>
  <div class="abs bottom">© 2023 Brightwell Aero Repair Services. All Rights Reserved.</div>
</footer>

</body>
</html>
```